Flight school sign for building, banner, and bilboard

This sign is primarily for use on the side of our flight school building to draw attention for current and future flight school students. We offer airplane and helicopter flight training, ground school training and seminars, airplane and helicopter rentals, multi-engine training, and more. I would like a professional but exciting sign that can be used across a multitude of signage options such as banners, banner ads, billboard, and other mediums so that our sign is consistent and recognizable.

Contact Information for Business Card

The business card should match our company sign somewhat but not exactly. We want good and exciting imagery or wording and energizing/exciting colors.

```html
<!DOCTYPE html>
<html lang="en">
<head>
<meta charset="utf-8">
<title>Zorvell Aviation – Building Sign</title>
<link href="https://fonts.googleapis.com/css2?family=Montserrat:wght@600;700;800&display=swap" rel="stylesheet">
<style>
  :root {
    --brand-red: #e8263a;
    --brand-navy: #272d57;
    --ink: #2a2a2a;
    --white: #ffffff;
    --backdrop: #eceef1;
  }
  * { box-sizing: border-box; margin: 0; padding: 0; }
  html, body { width: 900px; height: 1200px; overflow: hidden; }
  body {
    background: var(--backdrop);
    font-family: "Montserrat", Arial, sans-serif;
    position: relative;
  }
  .sign {
    position: absolute;
    left: 60px;
    top: 361px;
    width: 780px;
    height: 478px;
    background: var(--white);
    box-shadow: 0 4px 14px rgba(0,0,0,0.18);
    overflow: hidden;
  }
  .brand-mark {
    position: absolute;
    top: 145px;
    left: 0;
    width: 100%;
    display: flex;
    justify-content: center;
    align-items: center;
    gap: 12px;
  }
  .brand-mark__dot {
    width: 16px; height: 16px;
    border-radius: 50%;
    background: var(--brand-red);
  }
  .brand-mark__name {
    color: var(--brand-red);
    font-weight: 600;
    font-size: 28px;
    line-height: 1;
    letter-spacing: 0.5px;
  }
  .rule {
    position: absolute;
    height: 7px;
    background: var(--brand-navy);
  }
  .rule--top { left: 0; top: 198px; width: 394px; }
  .rule--bottom { right: 0; top: 352px; width: 394px; }
  .banner {
    position: absolute;
    left: 0; top: 205px;
    width: 100%; height: 147px;
    background: var(--brand-red);
    color: var(--white);
    text-align: center;
  }
  .banner__title {
    margin-top: 22px;
    font-weight: 800;
    font-size: 60px;
    line-height: 1;
    letter-spacing: 1px;
  }
  .banner__tagline {
    margin-top: 12px;
    font-weight: 700;
    font-size: 33px;
    line-height: 1;
  }
  .contacts {
    position: absolute;
    left: 0; top: 382px;
    width: 100%;
  }
  .contact {
    position: absolute;
    top: 0;
    width: 250px;
    margin-left: -125px;
    text-align: center;
  }
  .contact--phone { left: 127px; }
  .contact--email { left: 388px; }
  .contact--web { left: 635px; }
  .contact__icon {
    display: block;
    width: 32px; height: 32px;
    margin: 0 auto 8px;
  }
  .contact__text {
    font-weight: 700;
    font-size: 13px;
    color: var(--ink);
    white-space: nowrap;
  }
</style>
</head>
<body>
  <main class="sign">
    <div class="brand-mark">
      <span class="brand-mark__dot"></span>
      <span class="brand-mark__name">ZORVELL AVIATION</span>
    </div>

    <div class="rule rule--top"></div>
    <section class="banner">
      <h1 class="banner__title">ZORVELL AVIATION</h1>
      <p class="banner__tagline">Small step today,Giant leap tomorrow</p>
    </section>
    <div class="rule rule--bottom"></div>

    <section class="contacts">
      <div class="contact contact--phone">
        <svg class="contact__icon" viewBox="0 0 32 32" aria-hidden="true">
          <circle cx="16" cy="16" r="16" fill="#272d57"/>
          <path d="M11.5 8.5l2.6 0 1.2 3.6-1.8 1.4c.9 2 2.4 3.6 4.5 4.6l1.4-1.8 3.6 1.2v2.6c0 .9-.8 1.6-1.7 1.5C15.5 21.2 10.8 16.5 10 10.2c-.1-.9.6-1.7 1.5-1.7z" fill="#fff"/>
          <path d="M18 9.5a5 5 0 0 1 4.5 4.5M18 12a2.5 2.5 0 0 1 2 2" stroke="#fff" stroke-width="1.3" fill="none" stroke-linecap="round"/>
        </svg>
        <span class="contact__text">(555) 012 0147</span>
      </div>
      <div class="contact contact--email">
        <svg class="contact__icon" viewBox="0 0 32 32" aria-hidden="true">
          <circle cx="16" cy="16" r="16" fill="#272d57"/>
          <rect x="8.5" y="10.5" width="15" height="11" rx="1.2" fill="#fff"/>
          <path d="M9 11.2l7 5.6 7-5.6" stroke="#272d57" stroke-width="1.4" fill="none"/>
        </svg>
        <span class="contact__text">info@zorvellaviation.example</span>
      </div>
      <div class="contact contact--web">
        <svg class="contact__icon" viewBox="0 0 32 32" aria-hidden="true">
          <circle cx="16" cy="16" r="16" fill="#272d57"/>
          <g stroke="#fff" stroke-width="1.4" fill="none">
            <circle cx="16" cy="16" r="7.5"/>
            <ellipse cx="16" cy="16" rx="3.3" ry="7.5"/>
            <path d="M8.5 16h15M9.6 12.2h12.8M9.6 19.8h12.8"/>
          </g>
        </svg>
        <span class="contact__text">www.zorvellaviation.example</span>
      </div>
    </section>
  </main>
</body>
</html>
```